German Headhunter/ HR Consultancy needs Business Cards Design

We need a business Card Design for our Company in Stuttgart. We are specialized as Headhunter/ HR Consultancy in Placement of specialist and managers in permanent employment. Please refer to our business logo.

```html
<!DOCTYPE html>
<html lang="en">
<head>
<meta charset="utf-8">
<title>Kernwerk Personalberatung – Business Card</title>
<link rel="stylesheet" href="https://fonts.googleapis.com/css2?family=Montserrat:wght@500;600;700&family=Work+Sans:wght@400;500&display=swap">
<style>
  :root {
    --backdrop: #d6d7da;
    --card-white: #f7f7f6;
    --brand-blue: #2b46a3;
    --brand-blue-deep: #23398f;
    --brand-blue-bright: #1d3fe0;
    --ink: #3f4248;
    --ink-soft: #62666d;
    --on-blue: #e4e8f6;
  }
  * { box-sizing: border-box; margin: 0; padding: 0; }
  html, body { width: 1200px; height: 800px; overflow: hidden; }
  body {
    background: var(--backdrop);
    display: flex;
    align-items: center;
    justify-content: center;
    gap: 40px;
    font-family: "Work Sans", sans-serif;
  }
  .card {
    position: relative;
    width: 540px;
    height: 308px;
    border-radius: 20px;
    overflow: hidden;
  }

  /* Front */
  .card--front { background: var(--card-white); }
  .name-band {
    position: absolute;
    left: 0; top: 24px;
    width: 318px; height: 52px;
  }
  .name-band svg { display: block; }
  .name-band__text {
    position: absolute;
    left: 24px; top: 8px;
    color: #fff;
    font-family: "Montserrat", sans-serif;
  }
  .person-name {
    font-weight: 700;
    font-size: 17px;
    letter-spacing: 0.06em;
    text-transform: uppercase;
    line-height: 1.1;
  }
  .person-title {
    font-size: 11px;
    font-weight: 500;
    letter-spacing: 0.03em;
    margin-top: 2px;
  }
  .brand-lockup {
    position: absolute;
    left: 330px; top: 24px;
    display: flex;
    align-items: center;
    gap: 10px;
  }
  .brand-lockup__square {
    width: 26px; height: 26px;
    background: var(--brand-blue);
    flex: none;
  }
  .brand-lockup__name {
    font-family: "Montserrat", sans-serif;
    font-weight: 600;
    color: var(--brand-blue);
    line-height: 1.15;
  }
  .brand-lockup__name .main { display: block; font-size: 20px; letter-spacing: 0.06em; }
  .brand-lockup__name .sub { display: block; font-size: 9.5px; letter-spacing: 0.12em; }
  .address {
    position: absolute;
    right: 26px; top: 150px;
    text-align: right;
    font-size: 11.5px;
    line-height: 1.5;
    color: var(--ink);
    font-style: normal;
  }
  .address .web { color: var(--brand-blue); }
  .contacts {
    position: absolute;
    left: 40px; bottom: 26px;
    list-style: none;
    font-size: 11.5px;
    line-height: 1.55;
    color: var(--ink);
  }
  .contacts li { display: flex; align-items: center; gap: 8px; }
  .contacts svg { width: 10px; height: 10px; fill: var(--brand-blue); flex: none; }

  /* Back */
  .card--back {
    background: linear-gradient(135deg, var(--brand-blue) 0%, var(--brand-blue-deep) 100%);
  }
  .back-mark {
    position: absolute;
    left: 220px; top: 108px;
    font-family: "Montserrat", sans-serif;
    font-weight: 700;
    font-size: 44px;
    letter-spacing: 0.05em;
    color: var(--brand-blue-bright);
  }
  .tagline {
    position: absolute;
    left: 26px; bottom: 24px;
    width: 300px;
    font-size: 11px;
    line-height: 1.45;
    color: var(--on-blue);
  }
</style>
</head>
<body>

<section class="card card--front" aria-label="Business card front">
  <div class="name-band">
    <svg width="318" height="52" viewBox="0 0 318 52" aria-hidden="true">
      <polygon points="0,0 292,0 318,26 292,52 0,52" fill="var(--brand-blue)"/>
    </svg>
    <div class="name-band__text">
      <p class="person-name">Jonas Albrecht</p>
      <p class="person-title">Founder &amp; CEO</p>
    </div>
  </div>

  <div class="brand-lockup">
    <span class="brand-lockup__square" aria-hidden="true"></span>
    <p class="brand-lockup__name">
      <span class="main">KERNWERK</span>
      <span class="sub">PERSONALBERATUNG</span>
    </p>
  </div>

  <address class="address">
    Kernwerk Personalberatung<br>
    214 Maple Ridge Road<br>
    Fairbanks, Alaska 99701<br>
    <span class="web">www.kernwerk.com</span>
  </address>

  <ul class="contacts">
    <li><svg viewBox="0 0 10 10" aria-hidden="true"><path d="M2 0h2l1 2.5-1.3 1a5 5 0 0 0 2.8 2.8l1-1.3L10 6v2a2 2 0 0 1-2 2A8 8 0 0 1 0 2a2 2 0 0 1 2-2z"/></svg>555-201-4470</li>
    <li><svg viewBox="0 0 10 10" aria-hidden="true"><path d="M2 0h6v10H2zM3 1v7h4V1z"/></svg>555-318-2265</li>
    <li><svg viewBox="0 0 10 10" aria-hidden="true"><path d="M1 3h8v7H1zM3 0h4v3H3z"/></svg>555-642-0917</li>
    <li><svg viewBox="0 0 10 10" aria-hidden="true"><path d="M0 2h10v7H0zM1 3l4 3 4-3v-.2H1z"/></svg>jonas@kernwerk.com</li>
  </ul>
</section>

<section class="card card--back" aria-label="Business card back">
  <p class="back-mark">KERNWERK</p>
  <p class="tagline">We are specialized as Headhunter/ HR Consultancy in Placement of specialist &amp; managers in permanent employment.</p>
</section>

</body>
</html>
```